Logo Tweaks & Stationery Design Project for Energy Management Co

We are a specialist metering company trading for over 60 years and have recently developed GPRS metering infrastructure & monitoring services. For more information please see http://www.kestrel-vale.example/remote-meter-reading.html

Due to the success of this system it’s become necessary to open a new company “Brightwell Gauge Ltd” and this project is for relevant stationary designs for our documents.

I need something modern and clear to match our new logo style. Feel free to play around with the colors and tweak the logo if you like.

Maybe with some line chart animation on the header relating to our online services. ( See inspiration file )

Thanks
Derek

Target Market(s)

Renewable Energy Generation Monitoring, Energy Management, Remote Monitoring and Tennant Billing.

Industry/Entity Type

It Company

Requirements
Nice to have
• 100% Carbon neutral hosting
Should not have
• "Clip-Art" should not be used.

```html
<!DOCTYPE html>
<html lang="en">
<head>
<meta charset="utf-8">
<title>Brightwell Gauge — Letterhead</title>
<link rel="stylesheet" href="https://fonts.googleapis.com/css2?family=Michroma&display=swap">
<style>
  :root {
    --backdrop: #ece7de;
    --paper: #ffffff;
    --brand-red: #be1e2d;
    --brand-blue: #2b3990;
    --brand-blue-faint: #d3d9ea;
    --footer-grey: #6d6e71;
    --footer-text: #ffffff;
    --shadow: rgba(0, 0, 0, 0.35);
  }
  * { box-sizing: border-box; margin: 0; padding: 0; }
  html, body {
    width: 960px;
    height: 1200px;
    overflow: hidden;
    background: var(--backdrop);
  }
  .canvas {
    position: relative;
    width: 960px;
    height: 1200px;
  }
  .letterhead {
    position: absolute;
    left: 151px;
    top: 136px;
    width: 658px;
    height: 927px;
    background: var(--paper);
    box-shadow: 5px 6px 8px var(--shadow);
    overflow: hidden;
  }
  .letterhead__header {
    position: absolute;
    left: 0; top: 0;
    width: 100%;
    height: 119px;
    background: var(--brand-red);
    display: flex;
    align-items: center;
    justify-content: space-between;
    padding: 0 34px 0 20px;
  }
  .brand-name {
    font-family: "Michroma", sans-serif;
    font-weight: 400;
    color: var(--brand-blue);
    font-size: 30px;
    letter-spacing: 1px;
    text-transform: uppercase;
    line-height: 1;
    white-space: nowrap;
  }
  .brand-mark {
    width: 46px;
    height: 46px;
    background: var(--brand-blue);
  }
  .letterhead__watermark {
    position: absolute;
    left: 0; right: 0;
    top: 440px;
    text-align: center;
    font-family: "Michroma", sans-serif;
    font-weight: 400;
    color: var(--brand-blue-faint);
    font-size: 64px;
    line-height: 1.3;
    text-transform: uppercase;
  }
  .letterhead__footer {
    position: absolute;
    left: 0; bottom: 0;
    width: 100%;
    height: 36px;
    background: var(--footer-grey);
    display: flex;
    align-items: center;
    justify-content: center;
  }
  .footer-company {
    font-family: "Michroma", sans-serif;
    font-weight: 400;
    color: var(--footer-text);
    font-size: 13px;
    letter-spacing: 1px;
    line-height: 1;
    white-space: nowrap;
  }
</style>
</head>
<body>
  <main class="canvas">
    <article class="letterhead">
      <header class="letterhead__header">
        <span class="brand-name">Brightwell Gauge</span>
        <span class="brand-mark" aria-hidden="true"></span>
      </header>

      <div class="letterhead__watermark" aria-hidden="true">Brightwell<br>Gauge</div>

      <footer class="letterhead__footer">
        <span class="footer-company">Brightwell Gauge Ltd</span>
      </footer>
    </article>
  </main>
</body>
</html>
```